Corvane Automotive Reconditioning Business Card

We need a professional business card that features our logo, a picture of the employee, and a brief list of our services.
I've attached a logo, and will attach photos at a later date.
The four services that need to be listed are Bumper repair and repainting, road rash repair, clear coat scratch repair, and automotive touch-up.
Target Market(s)
30 - 40 year male general managers of automobile dealerships. They are used to seeing every vendor gimmick under the sun. This brochure needs to impress with its simplicity and honesty.
Industry/Entity Type
Automotive
Look and feel

```html
<!DOCTYPE html>
<html lang="en">
<head>
<meta charset="utf-8">
<title>Corvane Automotive Reconditioning – Business Card</title>
<link href="https://fonts.googleapis.com/css2?family=Open+Sans:wght@400;600;700;800&display=swap" rel="stylesheet">
<style>
  :root{
    --page:#e4e4e2;
    --white:#ffffff;
    --ink:#2b2b2b;
    --charcoal:#2e2e2e;
    --orange:#f05a1a;
    --wood-dark:#6f6155;
    --wood-mid:#8d7f72;
    --wood-light:#a39687;
    --photo-suit:#3d5a8a;
    --photo-bg:#f1f1f1;
  }
  *{box-sizing:border-box;margin:0;padding:0}
  html,body{width:1200px;height:800px;overflow:hidden}
  body{
    background:var(--page);
    font-family:"Open Sans",Arial,sans-serif;
    color:var(--ink);
    display:flex;align-items:center;justify-content:center;gap:50px;
  }
  .card{
    position:relative;width:525px;height:300px;border-radius:22px;overflow:hidden;
    box-shadow:0 10px 24px rgba(0,0,0,.18);
  }

  /* back */
  .card-back .wood{
    position:absolute;inset:0;
    background:linear-gradient(100deg,var(--wood-mid),var(--wood-light) 45%,var(--wood-dark));
  }
  .card-back .brand{position:absolute;left:0;right:0;top:88px;text-align:center}
  .brand-name{font-weight:800;font-size:64px;letter-spacing:3px;line-height:1;color:var(--charcoal);text-transform:uppercase}
  .brand-tag{font-weight:800;font-size:15px;letter-spacing:1.5px;color:var(--charcoal);margin-top:6px;text-transform:uppercase}
  .services-band{position:absolute;left:0;bottom:40px;width:100%;height:46px}
  .services{
    position:absolute;left:14px;right:10px;bottom:60px;
    font-size:9px;line-height:1.2;color:var(--ink);white-space:nowrap;
  }

  /* front */
  .card-front{background:var(--white)}
  .photo{
    position:absolute;left:40px;top:22px;width:180px;height:215px;
    background:linear-gradient(180deg,var(--photo-bg) 0%,#c9ced8 35%,var(--photo-suit) 70%,#2c4470 100%);
    border-radius:4px;
  }
  .front-band{position:absolute;left:0;bottom:30px;width:100%;height:50px}
  .person-name{
    position:absolute;left:30px;bottom:52px;color:var(--white);
    font-weight:600;font-size:15px;letter-spacing:2.5px;text-transform:uppercase;
  }
  .front-brand{position:absolute;right:28px;top:34px;text-align:center}
  .front-brand .brand-name{font-size:42px;letter-spacing:2px}
  .front-brand .brand-tag{font-size:10px;letter-spacing:1px;margin-top:4px}
  .contact{position:absolute;left:262px;top:114px;font-size:12px;line-height:1.35;list-style:none}
  .contact li{display:flex;align-items:center;gap:7px}
  .contact .address{display:block;margin-bottom:4px}
  .contact svg{width:11px;height:11px;flex:none;fill:var(--orange)}
</style>
</head>
<body>

  <section class="card card-back" aria-label="Card back">
    <div class="wood" role="img" aria-label="Brushed wood grain texture"></div>
    <div class="brand">
      <div class="brand-name">Corvane</div>
      <div class="brand-tag">Automotive Reconditioning</div>
    </div>
    <svg class="services-band" viewBox="0 0 525 46" preserveAspectRatio="none" aria-hidden="true">
      <polygon points="0,0 525,0 525,34 0,34" fill="#ffffff"/>
      <polygon points="0,34 525,34 525,38 0,38" fill="#f05a1a"/>
    </svg>
    <p class="services">Bumper repair and repainting | Road rash repair | Clear coat scratch repair | Automotive touch-up</p>
  </section>

  <section class="card card-front" aria-label="Card front">
    <div class="photo" role="img" aria-label="Portrait photo of the employee in a blue suit"></div>
    <svg class="front-band" viewBox="0 0 525 50" preserveAspectRatio="none" aria-hidden="true">
      <polygon points="0,0 500,22 500,50 0,50" fill="#2e2e2e"/>
      <polygon points="0,-3 500,19 500,22 0,0" fill="#f05a1a"/>
    </svg>
    <p class="person-name">Daniel Harlow</p>

    <div class="front-brand">
      <div class="brand-name">Corvane</div>
      <div class="brand-tag">Automotive Reconditioning</div>
    </div>

    <ul class="contact">
      <li class="address">4820 E. Linden Dr.<br>Mesa, AZ 85205</li>
      <li><svg viewBox="0 0 12 12"><path d="M2 1h3l1 3-2 1a7 7 0 0 0 3 3l1-2 3 1v3c-6 0-9-3-9-9z"/></svg>555-214-0370</li>
      <li><svg viewBox="0 0 12 12"><rect x="3" y="0.5" width="6" height="11" rx="1.2"/></svg>555-214-0380</li>
      <li><svg viewBox="0 0 12 12"><path d="M0.5 2.5h11v7h-11z M1 3l5 4 5-4" stroke="#fff" stroke-width="0.8"/></svg>info@corvaneauto.com</li>
      <li><svg viewBox="0 0 12 12"><circle cx="6" cy="6" r="5.5"/></svg>www.corvaneauto.com</li>
    </ul>
  </section>

</body>
</html>
```